IV Nutritional Clinic Web Design

We are working with Velqo. They are an IV Nutritional Clinic and in need of a new website design.
Some sites to use for inspiration:
https://brightpathcareco.com
https://www.ourzavrowellness.com
https://www.dewspringlounge.com
https://qvitalsurge.com
https://www.lumo-vital.com/pages/iv-therapy-west-hollywood
https://www.tqoncologyhub.com/cancer-care/iv-drips/
https://dripwellary.com
https://corvinahealthhub.com
Thank you for taking the time to consider designing a website for us. We are web developers based in Stockton, CA, USA. Most of our projects go through the same process. Understanding this process may help you win a project with us. We custom-code all of our websites in-house. We don’t have any requirements as to what tools you use for your design, but we prefer Figma files. For any design that we label as four-stars, we send it to the client for review. The client picks the final design they want us to use. Once we complete this process, we will continue to show additional clients all the four-star sites and purchase them later. Your designs will have multiple chances to sell. For better chances of success, we ask that you follow these guidelines.
IMAGES:
If you use any images or icons in the design, we ask that you have a link to the asset so we can purchase the image/icon. Most of the designs we submit do not have the customer’s images on them unless they have some great images. Be creative; show us the feeling you are trying to portray with your image choices. Use any royalty-free site you choose. We subscribe to Pixvane and mainly use their images, but we can purchase images outside of Pixvane.
PLEASE NOTE: we will not submit designs to clients with watermarks on the images.
FONTS:
We ask that you identify the fonts used in the design. This can be done in a message if you want. We typically use Google Fonts and Pixvane Fonts.
CONTENT:
We're always open to different content and ideas. We often submit designs with stock images so the client can see our vision. We typically take pictures after the website launch to use their images with our vision. Lorem Ipsum is fine for paragraphs, but we ask that you write the headers in correct English. We want to be able to show the vision and identify the sections of the website.
INSPIRATION:
We typically add a couple of links in the brief of websites we like to help you get started in your design.
REVISIONS:
We do not often ask for revisions of the designs unless we see something in the design that may not appeal to the client. If there are slight changes that we want to make, we do that in the development process.
FEEDBACK:
We rarely give feedback on designs during the design process. We are working on many website projects and do not have the time to provide feedback. We usually respond if your request is well thought out and asks specific questions, but a note asking “feedback, please” usually goes unanswered.

```html
<!DOCTYPE html>
<html lang="en">
<head>
<meta charset="utf-8">
<title>Velqo – IV Nutritional Clinic</title>
<link href="https://fonts.googleapis.com/css2?family=Lato:wght@400;700;900&display=swap" rel="stylesheet">
<style>
:root{
  --navy:#1c2580;
  --panel:#3545a0;
  --green:#7aa743;
  --text:#555;
  --heading:#555a5e;
  --border:#e6e6e6;
  --footer:#575757;
  --white:#fff;
}
*{box-sizing:border-box;margin:0;padding:0}
html,body{width:1200px;height:4217px;overflow:hidden}
body{font-family:'Lato',sans-serif;color:var(--text);background:var(--white);position:relative}
.abs{position:absolute}
.topline{top:0;left:0;width:1200px;height:4px;background:var(--green)}
.logo{left:111px;top:34px;display:flex;align-items:center;gap:12px}
.logo-mark{width:18px;height:18px;background:var(--green);display:block}
.logo-name{font-weight:900;font-size:46px;letter-spacing:1px;color:var(--navy);line-height:1}
.contact-bar{top:26px;right:112px;display:flex;gap:34px;font-size:14px;color:#666}
.contact-bar span{display:flex;align-items:center;gap:10px}
.nav{top:76px;right:112px;display:flex;gap:56px;font-size:15px;color:#555;align-items:center}
.nav .active{background:var(--navy);color:var(--white);padding:6px 12px;margin-right:-10px}
.hero{top:128px;left:0;width:1200px;height:600px;background:linear-gradient(110deg,#ccd0d4,#eef0f2 45%,#d8dcdf)}
.hero-panel{top:216px;left:111px;width:622px;height:424px;background:rgba(45,60,160,.88);padding:50px 77px;color:var(--white)}
.hero-panel h1{font-size:49px;font-weight:900;line-height:1.07;text-transform:uppercase}
.hero-panel p{font-size:16px;line-height:1.6;margin-top:24px;width:430px}
.btn{display:inline-block;background:var(--green);color:var(--white);font-size:15px;padding:9px 27px}
.hero-panel .btn{margin-top:26px}
.sec-title{left:0;width:1200px;text-align:center;font-size:39px;font-weight:900;color:var(--heading);text-transform:uppercase}
.sec-title b{color:var(--navy);font-weight:900}
.sec-title::after{content:"";display:block;width:98px;height:4px;background:var(--green);margin:8px auto 0}
.sec-lead{left:230px;width:740px;text-align:center;font-size:16px;line-height:1.55;color:#666}
.cards{left:111px;width:977px;display:grid;grid-template-columns:repeat(3,291px);column-gap:52px;row-gap:46px}
.card{height:313px;border:1px solid var(--border);padding:33px 28px 0;background:var(--white)}
.card .ico{width:82px;height:82px;background:#e9ebf5;display:flex;align-items:center;justify-content:center}
.card h3{margin-top:40px;font-size:19px;font-weight:700;color:#444;border-left:3px solid var(--green);padding-left:12px;line-height:1}
.card p{margin-top:20px;font-size:14.5px;line-height:1.65;color:#555}
.card.featured{background:var(--green);border-color:var(--green)}
.card.featured .ico{background:var(--white)}
.card.featured h3,.card.featured p{color:var(--white);border-left-color:var(--white)}
.about-title{left:111px;top:1745px;font-size:39px;font-weight:900;color:var(--heading)}
.about-title b{color:var(--navy)}
.about-title::after{content:"";display:block;width:98px;height:4px;background:var(--green);margin-top:8px}
.about-text{left:111px;top:1838px;width:430px;font-size:14.5px;line-height:1.65}
.about-text p+p{margin-top:24px}
.about-text .btn{margin-top:26px}
.about-img{left:609px;top:1738px;width:476px;height:472px;background:linear-gradient(150deg,#d9dde2,#b9c0c8 60%,#c9ced3)}
.cta{left:64px;top:2295px;width:1072px;height:327px;background:var(--navy);padding:50px 47px;color:var(--white)}
.cta h2{font-size:39px;font-weight:900;line-height:1.07;text-transform:uppercase;width:560px}
.cta .rule{width:98px;height:4px;background:var(--white);margin:20px 0 24px}
.cta p{font-size:16px;line-height:1.55;width:480px}
.cta-actions{display:flex;align-items:center;gap:24px;margin-top:26px;font-size:15px}
.cta-actions span{display:flex;align-items:center;gap:10px}
.cta-img{left:712px;top:2328px;width:393px;height:263px;background:linear-gradient(120deg,#c9d4e6,#e8edf3 50%,#aab8cf)}
.blog{left:111px;top:2874px;width:977px;display:grid;grid-template-columns:repeat(3,303px);column-gap:34px;text-align:center}
.blog .thumb{height:240px}
.blog h3{margin-top:20px;font-size:21px;font-weight:700;color:var(--navy)}
.blog p{margin-top:14px;font-size:14.5px;line-height:1.6;padding:0 18px}
.blog .btn{margin-top:20px}
.dots{top:3329px;left:553px;display:flex;gap:10px}
.dots i{width:25px;height:9px;background:#666;display:block}
.dots i:first-child{background:var(--green)}
.reviews{left:111px;top:3498px;width:977px;display:grid;grid-template-columns:repeat(3,318px);column-gap:12px}
.review{height:228px;border:1px solid var(--border);padding:30px 24px;background:#fcfcfc;font-size:14.5px;line-height:1.55}
.review .stars{color:#f08a1c;letter-spacing:1px;font-size:15px}
.review p{margin-top:16px}
.review h4{margin-top:18px;font-size:17px;font-weight:400;color:var(--green)}
.review small{display:block;margin-top:8px;font-size:12px}
.review.active{background:var(--navy);color:var(--white);border-color:var(--navy)}
.review.active .stars,.review.active h4{color:var(--white)}
.arrow{width:34px;height:34px;border-radius:50%;background:var(--green);top:3588px;display:flex;align-items:center;justify-content:center}
.footer{left:0;top:3811px;width:1200px;height:406px;background:var(--footer);color:var(--white)}
.fcol{top:70px;font-size:14.5px;line-height:1.8}
.fcol h4{font-size:21px;font-weight:700;margin-bottom:14px}
.fcol ul{list-style:none}
.fcol li{margin-bottom:10px}
.fcontact li{display:flex;gap:20px;margin-bottom:26px}
.social{display:flex;gap:14px;margin-top:28px}
.social i{width:30px;height:30px;border-radius:50%;background:rgba(255,255,255,.85);display:block}
.footer .divider{left:0;top:355px;width:1200px;height:1px;background:#6a6a6a}
.copyright{top:366px;left:0;width:1200px;text-align:center;font-size:12px}
</style>
</head>
<body>
<div class="abs topline"></div>

<header>
  <div class="abs logo">
    <span class="logo-mark"></span>
    <span class="logo-name">Velqo</span>
  </div>
  <div class="abs contact-bar">
    <span><svg width="22" height="22" viewBox="0 0 22 22"><rect width="22" height="22" rx="3" fill="#7aa743"/><path d="M7 5l3 3-1.5 2c1 2 2 3 3.5 3.5l2-1.5 3 3-1.5 2C9 16 6 13 5 6.5z" fill="#fff"/></svg>Call Us : + 1 888 888 8888</span>
    <span><svg width="26" height="20" viewBox="0 0 26 20"><rect width="26" height="20" rx="2" fill="#7aa743"/><path d="M2 3l11 8 11-8" stroke="#fff" stroke-width="2" fill="none"/></svg>Email : info@velqohydration.com</span>
  </div>
  <nav class="abs nav">
    <span class="active">Home</span><span>About Us</span><span>IV Therapy</span><span>Blog</span><span>Team</span><span>Contact Us</span>
  </nav>
</header>

<section class="abs hero" role="img" aria-label="Patient resting with an IV drip line in a bright clinic room"></section>
<div class="abs hero-panel">
  <h1>Revitalize Your Body With IV Therapy</h1>
  <p>Boost your energy, enhance immunity, and hydrate faster with our tailored IV nutrient infusions. Experience wellness like never before.</p>
  <span class="btn">Book Now</span>
</div>

<h2 class="abs sec-title" style="top:806px">Our <b>Treatments</b></h2>
<p class="abs sec-lead" style="top:880px">Optimize your health with our customized IV drips, designed to hydrate, energize, and rejuvenate your body from the inside out. Experience faster recovery, enhanced immunity, and peak performance—one drip at a time.</p>

<div class="abs cards" style="top:980px">
  <div class="card"><div class="ico"><svg width="44" height="44" viewBox="0 0 44 44" fill="none" stroke="#1c2580" stroke-width="2"><rect x="6" y="8" width="32" height="28" rx="4"/><path d="M6 28h32M12 28v-4M18 28v-3M24 28v-4M30 28v-3"/></svg></div><h3>Weight Loss</h3><p>Lorem ipsum dolor sit amet, consectetur adipiscing elit, sed do eiusmod tempor incididunt ut labore et dolore magna aliqua.</p></div>
  <div class="card"><div class="ico"><svg width="44" height="44" viewBox="0 0 44 44" fill="none" stroke="#1c2580" stroke-width="2"><path d="M22 6c6 9 10 14 10 20a10 10 0 0 1-20 0c0-6 4-11 10-20z"/><circle cx="20" cy="27" r="2"/><circle cx="25" cy="31" r="2"/></svg></div><h3>Peptide Therapy</h3><p>Lorem ipsum dolor sit amet, consectetur adipiscing elit, sed do eiusmod tempor incididunt ut labore et dolore magna aliqua.</p></div>
  <div class="card"><div class="ico"><svg width="44" height="44" viewBox="0 0 44 44" fill="none" stroke="#1c2580" stroke-width="2"><path d="M8 18l8-8 6 6 10-10M28 6h6v6"/><rect x="6" y="24" width="32" height="14" rx="3"/></svg></div><h3>Contourline RF</h3><p>Lorem ipsum dolor sit amet, consectetur adipiscing elit, sed do eiusmod tempor incididunt ut labore et dolore magna aliqua.</p></div>
  <div class="card"><div class="ico"><svg width="44" height="44" viewBox="0 0 44 44" fill="none" stroke="#1c2580" stroke-width="2"><rect x="10" y="6" width="16" height="22" rx="3"/><path d="M14 13h8M14 18h8M18 28v6a6 6 0 0 0 12 0v-4h6"/></svg></div><h3>IV Drip Infusions</h3><p>Lorem ipsum dolor sit amet, consectetur adipiscing elit, sed do eiusmod tempor incididunt ut labore et dolore magna aliqua.</p></div>
  <div class="card"><div class="ico"><svg width="44" height="44" viewBox="0 0 44 44" fill="none" stroke="#1c2580" stroke-width="2"><path d="M16 8l8 4v8l-8 4-8-4v-8zM28 20l8 4v8l-8 4-8-4v-8z"/></svg></div><h3>Methylene Blue IV</h3><p>Lorem ipsum dolor sit amet, consectetur adipiscing elit, sed do eiusmod tempor incididunt ut labore et dolore magna aliqua.</p></div>
  <div class="card featured"><div class="ico"><svg width="44" height="44" viewBox="0 0 44 44" fill="none" stroke="#1c2580" stroke-width="2"><circle cx="26" cy="14" r="9"/><path d="M26 9c2 3 3 4 3 6a3 3 0 0 1-6 0c0-2 1-3 3-6zM6 30h8l6 3h10l6-4"/></svg></div><h3>Peakline IV Boosters</h3><p>Lorem ipsum dolor sit amet, consectetur adipiscing elit, sed do eiusmod tempor incididunt ut labore et dolore magna aliqua.</p></div>
</div>

<h2 class="abs about-title">ABOUT <b>US</b></h2>
<div class="abs about-text">
  <p>Lorem ipsum dolor sit amet, consectetur adipiscing elit, sed do eiusmod tempor incididunt ut labore et dolore magna aliqua. Ut enim ad minim veniam, quis nostrud exercitation ullamco lab oris nisi ut aliquip ex ea commodo consequat.</p>
  <p>Sed ut perspiciatis unde omnis iste natus error sit voluptatem accusantium doloremque laudantium, totam rem aperiam, eaque ipsa quae ab illo inventore veritatis et quasi architecto beatae vitae dicta sunt explicabo.Sed ut perspiciatis unde omnis iste natus error sit voluptatem accusantium doloremque lau dantium, totam rem aperiam, eaque ipsa quae ab illo inventore veritatis et quasi architecto beatae vitae dicta sunt explicabo.</p>
  <span class="btn">Read More</span>
</div>
<div class="abs about-img" role="img" aria-label="Nurse in gloves setting an IV drip for a relaxed client in a white robe"></div>

<section class="abs cta">
  <h2>Are You Ready To Elevate You Well-Being?</h2>
  <div class="rule"></div>
  <p>Lorem ipsum dolor sit amet, consectetur adipiscing elit, sed do eiusmod tempor incididunt ut labore et dolore magna aliqua.</p>
  <div class="cta-actions">
    <span class="btn">Schedule Appointment</span>
    <span><svg width="22" height="22" viewBox="0 0 22 22"><rect width="22" height="22" rx="3" fill="#7aa743"/><path d="M7 5l3 3-1.5 2c1 2 2 3 3.5 3.5l2-1.5 3 3-1.5 2C9 16 6 13 5 6.5z" fill="#fff"/></svg>Call Us : + 1 888 888 8888</span>
  </div>
</section>
<div class="abs cta-img" role="img" aria-label="Clinician preparing an IV infusion for a seated patient in a treatment room"></div>

<h2 class="abs sec-title" style="top:2701px">Our <b>Blog</b></h2>
<p class="abs sec-lead" style="top:2776px;left:250px;width:700px">Experience the power of IV nutrient therapy—scientifically formulated to enhance hydration, optimize recovery, and support overall health. Whether you need an energy boost, immune support, or post-workout recovery, we've got a drip for you.</p>

<div class="abs blog">
  <article><div class="thumb" role="img" aria-label="Patient lying in bed receiving an IV drip" style="background:linear-gradient(135deg,#b7c1cc,#e5e8ec 55%,#9fabb8)"></div><h3>IV Nutritional Clinic 1</h3><p>Excepteur sint occaecat cupidatat non proident, sunt in culpa qui officia deser mollit anim id est laborum.</p><span class="btn">Read More</span></article>
  <article><div class="thumb" role="img" aria-label="IV bag filled with fresh fruit slices" style="background:radial-gradient(circle at 50% 55%,#c9d27a,#dfe6f4 45%,#8e9fd0)"></div><h3>IV Nutritional Clinic 2</h3><p>Excepteur sint occaecat cupidatat non proident, sunt in culpa qui officia deser mollit anim id est laborum.</p><span class="btn">Read More</span></article>
  <article><div class="thumb" role="img" aria-label="Splash of clear water droplets on a light blue background" style="background:radial-gradient(circle,#e7f3f5,#a9d4da)"></div><h3>IV Nutritional Clinic 3</h3><p>Excepteur sint occaecat cupidatat non proident, sunt in culpa qui officia deser mollit anim id est laborum.</p><span class="btn">Read More</span></article>
</div>
<div class="abs dots"><i></i><i></i><i></i></div>

<h2 class="abs sec-title" style="top:3414px">What Our <b>Customers Say</b></h2>
<div class="abs arrow" style="left:52px"><svg width="14" height="14" viewBox="0 0 14 14"><path d="M9 2L4 7l5 5" stroke="#fff" stroke-width="2.5" fill="none"/></svg></div>
<div class="abs arrow" style="left:1113px"><svg width="14" height="14" viewBox="0 0 14 14"><path d="M5 2l5 5-5 5" stroke="#fff" stroke-width="2.5" fill="none"/></svg></div>
<div class="abs reviews">
  <div class="review"><div class="stars">★★★★★</div><p>Excepteur sint occaecat cupidatat non proident, sunt in culpa qui officia deserunt mollit anim id est laborum.</p><h4>Hallbrook</h4><small>Feb 20 2025</small></div>
  <div class="review active"><div class="stars">★★★★★</div><p>Excepteur sint occaecat cupidatat non proident, sunt in culpa qui officia deserunt mollit anim id est laborum.</p><h4>Lenna</h4><small>Feb 20 2025</small></div>
  <div class="review"><div class="stars">★★★★★</div><p>Excepteur sint occaecat cupidatat non proident, sunt in culpa qui officia deserunt mollit anim id est laborum.</p><h4>Marisol</h4><small>Feb 20 2025</small></div>
</div>

<footer class="abs footer">
  <div class="abs fcol" style="left:113px;width:260px">
    <h4>About Us</h4>
    <p>From beauty-enhancing infusions to powerful immunity boosters, each treatment is crafted to help you look, feel, and perform at your best.</p>
    <div class="social"><i></i><i></i><i></i><i></i></div>
  </div>
  <div class="abs fcol fcontact" style="left:427px;width:280px">
    <h4>Contact Us</h4>
    <ul>
      <li><svg width="16" height="22" viewBox="0 0 16 22" fill="none" stroke="#fff" stroke-width="1.5"><path d="M8 21s7-8 7-13A7 7 0 0 0 1 8c0 5 7 13 7 13z"/><circle cx="8" cy="8" r="2.5"/></svg><span>123,IV Nutritional Clinic<br>company Na 123456.</span></li>
      <li><svg width="18" height="18" viewBox="0 0 18 18" fill="none" stroke="#fff" stroke-width="1.5"><path d="M4 1l3 4-2 2c1 2.5 3 4.5 5 5l2-2 4 3-2 3C7 16 2 11 1 3z"/></svg><span>+ 1 888 888 8888</span></li>
      <li><svg width="18" height="14" viewBox="0 0 18 14" fill="none" stroke="#fff" stroke-width="1.5"><rect x="1" y="1" width="16" height="12"/><path d="M1 1l8 6 8-6"/></svg><span>info@velqoclinic.com</span></li>
    </ul>
  </div>
  <div class="abs fcol" style="left:758px">
    <h4>Quick Links</h4>
    <ul><li>Home</li><li>About Us</li><li>IV Therapy</li><li>Blog</li><li>Team</li></ul>
  </div>
  <div class="abs fcol" style="left:956px">
    <h4>Other Links</h4>
    <ul><li>Support</li><li>FAQs</li><li>Contact Us</li><li>Terms &amp; Conditions</li><li>Privacy Policy</li></ul>
  </div>
  <div class="abs divider"></div>
  <p class="abs copyright">Copyright © 2025 IV Nutritional Clinic . All Rights Reserved</p>
</footer>
</body>
</html>
```